design a construction company business card

Design business card around our logo. Card must have all the typical info: name, title, address, phone, email, business name, etc. Somewhere on the card I would like to see our motto "Built on integrity... Inspired by commitment." Consider adding a splash of bright orange to the card to complement the blues and silvers/grays in the logo. We are open to metallic inks, textures, etc. We would like to see options on both light and dark backgrounds. The font in the logo is Euro Technic Extended Regular.

```html
<!DOCTYPE html>
<html lang="en">
<head>
<meta charset="utf-8">
<title>Halden Contracting business cards</title>
<link rel="stylesheet" href="https://fonts.googleapis.com/css2?family=Michroma&family=Montserrat:wght@400;600;800&display=swap">
<style>
  :root {
    --backdrop: #1b1b1d;
    --card-dark: #28282b;
    --card-dark-edge: #1f1f22;
    --card-blue: #3a7cc8;
    --card-blue-light: #5a95d6;
    --logo-silver: #8e9096;
    --text-light: #f2f2f2;
    --text-soft: #d8dde4;
    --accent-blue: #2f6fc4;
    --accent-white: #ffffff;
  }
  * { box-sizing: border-box; margin: 0; padding: 0; }
  html, body { width: 1200px; height: 960px; overflow: hidden; }
  body {
    background: var(--backdrop);
    display: flex;
    align-items: center;
    justify-content: center;
    gap: 60px;
    font-family: "Montserrat", sans-serif;
  }
  .card {
    width: 525px;
    height: 300px;
    position: relative;
    overflow: hidden;
    box-shadow: 0 18px 40px rgba(0,0,0,0.55);
  }

  /* Front */
  .card-front {
    background: linear-gradient(135deg, var(--card-dark) 0%, #303034 55%, var(--card-dark-edge) 100%);
  }
  .front-brand {
    position: absolute;
    left: 38px;
    top: 42px;
    font-family: "Michroma", sans-serif;
    color: var(--logo-silver);
    font-size: 17px;
    letter-spacing: 1px;
    display: flex;
    align-items: center;
    gap: 10px;
  }
  .brand-mark {
    width: 14px;
    height: 14px;
    background: var(--logo-silver);
  }
  .contact-block {
    position: absolute;
    right: 42px;
    top: 118px;
    width: 230px;
    color: var(--text-light);
  }
  .person-name {
    font-weight: 800;
    font-size: 22px;
    letter-spacing: 2px;
    text-transform: uppercase;
  }
  .person-title {
    font-size: 11px;
    color: var(--text-soft);
    margin-bottom: 16px;
  }
  .contact-list { list-style: none; font-size: 12px; line-height: 18px; }
  .contact-list li { display: flex; align-items: center; gap: 8px; }
  .contact-list svg { width: 11px; height: 11px; fill: var(--text-light); flex: none; }
  .address {
    margin-top: 12px;
    font-size: 12px;
    margin-left: -20px;
  }
  .front-band {
    position: absolute;
    left: 0; right: 0; bottom: 0;
    height: 12px;
    display: flex;
  }
  .band-blue { flex: 0 0 62%; background: var(--accent-blue); }
  .band-white { flex: 1; background: var(--accent-white); }

  /* Back */
  .card-back {
    background: radial-gradient(circle at 60% 30%, var(--card-blue-light) 0%, var(--card-blue) 60%, #2f6dba 100%);
    display: flex;
    flex-direction: column;
    align-items: center;
    justify-content: center;
    gap: 22px;
  }
  .back-brand {
    font-family: "Michroma", sans-serif;
    color: #c9dcf2;
    font-size: 22px;
    letter-spacing: 1px;
    display: flex;
    align-items: center;
    gap: 12px;
  }
  .back-brand .brand-mark { background: #c9dcf2; width: 16px; height: 16px; }
  .motto {
    font-size: 11px;
    color: #d6e4f5;
    letter-spacing: 0.5px;
  }
</style>
</head>
<body>
  <section class="card card-front" aria-label="Business card front">
    <div class="front-brand"><span class="brand-mark"></span>Halden Contracting, Inc.</div>
    <div class="contact-block">
      <p class="person-name">Your Name</p>
      <p class="person-title">Your Title</p>
      <ul class="contact-list">
        <li><svg viewBox="0 0 24 24" aria-hidden="true"><path d="M6.6 10.8a15 15 0 0 0 6.6 6.6l2.2-2.2a1 1 0 0 1 1-.25 11.4 11.4 0 0 0 3.6.57 1 1 0 0 1 1 1V20a1 1 0 0 1-1 1A17 17 0 0 1 3 4a1 1 0 0 1 1-1h3.5a1 1 0 0 1 1 1 11.4 11.4 0 0 0 .57 3.6 1 1 0 0 1-.25 1z"/></svg>123-456-2100</li>
        <li><svg viewBox="0 0 24 24" aria-hidden="true"><path d="M2 5h20v14H2zm2 2v.5l8 5 8-5V7l-8 5z"/></svg>youremail@mailbox.com</li>
        <li><svg viewBox="0 0 24 24" aria-hidden="true"><circle cx="12" cy="12" r="10"/></svg>www.yourwebsite.com</li>
      </ul>
      <p class="address">Your address, city, state, ZIP 0000</p>
    </div>
    <div class="front-band"><span class="band-blue"></span><span class="band-white"></span></div>
  </section>

  <section class="card card-back" aria-label="Business card back">
    <div class="back-brand"><span class="brand-mark"></span>Halden Contracting, Inc.</div>
    <p class="motto">Built on integrity... Inspired by commitment.</p>
  </section>
</body>
</html>
```